Clean Vexlo Ads Banner Design For A Finance Company

Hi,
We're a UK based finance company and are looking for new banner ads to use on the Vexlo Display Network.
We want the end product to stand out by using strong, minimal design - ideally starting from a dark theme, although I'm open to ideas.
The copy should read:
'Fast Bridging Loans From 0.39% PM'
Once we have these designs agreed, we are looking to replicate them for other products, changing only the text on each ad - for example, 'commercial mortgage service you can rely on' or 'development finance service you can rely on'.
The colours used on our website are the following:
Black - #040303
Orange - #f79124
White - #ffffff
Grey - #ffffff
Example ads that I like - https://www.plimrake.com/wp-content/uploads/2021/07/vexlo-display-ads-example-2-final.png.webp
2 - https://qarnelvistahub.com/wp-content/uploads/2020/03/fbdd56ba3bd16c7a8debb13a411de786.jpg

```html
<!DOCTYPE html>
<html lang="en">
<head>
<meta charset="utf-8">
<title>Corvane Finance – Fast Bridging Loans</title>
<link rel="stylesheet" href="https://fonts.googleapis.com/css2?family=Bebas+Neue&display=swap">
<style>
  :root {
    --orange: #f79124;
    --orange-light: #fbb063;
    --black: #040303;
    --white: #ffffff;
    --sky-warm: #d08f3e;
    --sky-dusk: #8a5a2c;
    --city-dark: #241d19;
  }
  html, body {
    margin: 0;
    padding: 0;
    overflow: hidden;
  }
  .banner {
    position: relative;
    width: 1200px;
    height: 2398px;
    background: var(--orange);
    overflow: hidden;
    font-family: "Bebas Neue", "Oswald", sans-serif;
    color: var(--white);
  }
  .hero {
    position: absolute;
    left: 0;
    top: 0;
    width: 1200px;
    height: 870px;
    display: block;
  }
  .headline {
    position: absolute;
    left: 92px;
    top: 905px;
    margin: 0;
    font-size: 158px;
    line-height: 1;
    font-weight: 400;
    letter-spacing: 0.005em;
    white-space: nowrap;
  }
  .from {
    position: absolute;
    left: 94px;
    top: 1082px;
    margin: 0;
    font-size: 78px;
    line-height: 1;
    letter-spacing: 0.03em;
  }
  .rate {
    position: absolute;
    left: 82px;
    top: 1110px;
    margin: 0;
    font-size: 885px;
    line-height: 1;
    letter-spacing: -0.01em;
    transform: scaleX(0.8);
    transform-origin: left top;
    white-space: nowrap;
  }
  .rate-unit {
    position: absolute;
    left: 1050px;
    margin: 0;
    line-height: 1;
  }
  .rate-unit--percent { top: 1232px; font-size: 112px; }
  .rate-unit--period { top: 1674px; font-size: 118px; left: 1036px; }
  .brand {
    position: absolute;
    left: 0;
    top: 2030px;
    width: 1200px;
    margin: 0;
    text-align: center;
    font-size: 150px;
    line-height: 1;
    font-weight: 400;
    letter-spacing: 0.02em;
    color: var(--white);
    white-space: nowrap;
  }
</style>
</head>
<body>
  <main class="banner">
    <svg class="hero" viewBox="0 0 1200 870">
      <defs>
        <linearGradient id="skyline-tone" x1="0" y1="0" x2="0" y2="1">
          <stop offset="0" stop-color="var(--sky-warm)"/>
          <stop offset="0.3" stop-color="var(--sky-dusk)"/>
          <stop offset="0.55" stop-color="var(--city-dark)"/>
          <stop offset="1" stop-color="var(--city-dark)"/>
        </linearGradient>
      </defs>
      <polygon class="hero-band" points="0,441 600,767 1200,441 1200,527 600,853 0,527" fill="var(--orange-light)"/>
      <polygon class="hero-photo" role="img" aria-label="London skyline at sunset with a domed cathedral and lit office buildings under an orange sky" points="0,0 1200,0 1200,441 600,767 0,441" fill="url(#skyline-tone)"/>
    </svg>

    <h1 class="headline">Fast Bridging Loans</h1>
    <p class="from">From</p>
    <p class="rate">0.39</p>
    <p class="rate-unit rate-unit--percent">%</p>
    <p class="rate-unit rate-unit--period">PM</p>

    <p class="brand">Corvane Finance</p>
  </main>
</body>
</html>
```